Harborview Optical -Window Poster (Optometrist)

We are an optometry practice and we need a poster for a new store promotion for our window highlighting we now also sell 2 pairs of glasses as a package deal. The size will be 1300mm width x 1900mm height

The artwork will be displayed as a fabric banner in our shop window. We have 7 other banners with different services our business provides. The words needs to standout for passers by and the cars stopped at the traffic lights out front of our business. We already have signs with our logos phone number etc. so we won't need them included in the poster.

It would need to include the following information.

Two pair packages now available*

*Conditions apply

The artwork will be displayed as a fabric banner in our shop window. We have 7 other banners with different services our business provides. The words needs to standout for passers by and the cars stopped at the traffic lights out front of our business. We already have signs with our logos phone number etc. so we won't need them included in the poster. Thank you for your work it's amazing Added Saturday, February 18, 2017

The artwork will be displayed as a fabric banner in our shop window. We have 7 other banners with different services our business provides. The words needs to standout for passers by and the cars stopped at the traffic lights out front of our business. We already have signs with our logos phone number etc. so we won't need them included in the poster. Added Saturday, February 18, 2017

Target Market(s)

Cars driving past and stopped at traffic lights outside our store.

Industry/Entity Type

Optician

Requirements
Must have
• Poster must say:
• Two pair packages now available*
• *Conditions apply

```html
<!DOCTYPE html>
<html lang="en">
<head>
<meta charset="utf-8">
<title>Harborview Optical – Two Pair Packages Window Poster</title>
<link rel="stylesheet" href="https://fonts.googleapis.com/css2?family=Archivo+Black&family=Oswald:wght@400&family=Yellowtail&display=swap">
<style>
  :root {
    --burst-core: #e8862f;
    --burst-mid: #c4501f;
    --burst-edge: #8a2a16;
    --burst-corner: #5e1a0e;
    --gold-light: #fff06a;
    --gold: #f4c81c;
    --gold-deep: #d99a0c;
    --ink-white: #ffffff;
    --extrude: #2a0f0c;
    --script-yellow: #ffe23a;
  }
  html, body {
    margin: 0;
    padding: 0;
    width: 962px;
    height: 1200px;
    overflow: hidden;
    background: var(--burst-edge);
  }
  .poster {
    position: relative;
    width: 962px;
    height: 1200px;
    overflow: hidden;
    background:
      radial-gradient(ellipse 70% 60% at 50% 47%, var(--burst-core) 0%, var(--burst-mid) 55%, var(--burst-edge) 85%, var(--burst-corner) 100%);
  }
  .poster-art {
    position: absolute;
    inset: 0;
    width: 962px;
    height: 1200px;
  }
  .kicker {
    font-family: "Oswald", "Arial Narrow", sans-serif;
    font-weight: 400;
    font-size: 76px;
    fill: var(--ink-white);
    filter: drop-shadow(2px 3px 2px rgba(40, 10, 5, 0.55));
  }
  .pointer {
    fill: var(--gold);
    stroke: none;
    filter: drop-shadow(1px 2px 1px rgba(40, 10, 5, 0.5));
  }
  .headline {
    font-family: "Archivo Black", "Arial Black", sans-serif;
    font-size: 186px;
  }
  .headline-gold {
    fill: url(#goldFill);
    filter: drop-shadow(3px 5px 3px rgba(50, 12, 4, 0.6));
  }
  .headline-white { fill: var(--ink-white); }
  .headline-extrude { fill: var(--extrude); }
  .disclaimer {
    font-family: "Yellowtail", cursive;
    font-size: 92px;
    fill: var(--script-yellow);
    filter: drop-shadow(2px 4px 2px rgba(50, 12, 4, 0.6));
  }
</style>
</head>
<body>
<main class="poster" aria-label="Harborview Optical window poster">
  <svg class="poster-art" viewBox="0 0 962 1200" xmlns="http://www.w3.org/2000/svg">
    <defs>
      <linearGradient id="goldFill" x1="0" y1="0" x2="0" y2="1">
        <stop offset="0" stop-color="var(--gold-light)"/>
        <stop offset="0.55" stop-color="var(--gold)"/>
        <stop offset="1" stop-color="var(--gold-deep)"/>
      </linearGradient>
    </defs>

    <g class="offer-kicker">
      <path class="pointer" d="M118 209 h118 v-8 l20 12 l-20 12 v-8 h-118 z"/>
      <text class="kicker" x="274" y="244" textLength="486" lengthAdjust="spacingAndGlyphs">NOW AVAILABLE*</text>
      <path class="pointer" d="M914 209 h-118 v-8 l-20 12 l20 12 v-8 h118 z"/>
    </g>

    <text class="headline headline-gold" x="33" y="487" textLength="911" lengthAdjust="spacingAndGlyphs">TWO PAIR</text>

    <g class="headline-packages">
      <text class="headline headline-extrude" x="80" y="704" textLength="852" lengthAdjust="spacingAndGlyphs">PACKAGES</text>
      <text class="headline headline-extrude" x="77" y="699" textLength="852" lengthAdjust="spacingAndGlyphs">PACKAGES</text>
      <text class="headline headline-white" x="72" y="693" textLength="852" lengthAdjust="spacingAndGlyphs">PACKAGES</text>
    </g>

    <text class="disclaimer" x="167" y="862" textLength="618" lengthAdjust="spacingAndGlyphs">*Conditions apply</text>
  </svg>
</main>
</body>
</html>
```